Fitness Equipment & Service

I want to make the card eye catching and fun. We are called Corvane Motion Limited and we are based in Wales. We sell, install and service all types of fitness equipment from Skipping ropes, right through the Dumbbells, Kettle bells and Barbells through to state of the art Treadmills, Running Machines and Strength Equipment. We also design and install changing room furniture and lockers.

TYPOGRAPHY
We would like to use Futrura. Futura has an appearance of efficiency and forwardness. The typeface is derived
from simple geometric forms (near-perfect circles, triangles and squares) and is based on strokes of
near-even weight, which are low in contrast. This is most visible in the almost perfectly round stroke of
the o, which is nonetheless slightly ovoid.
The lowercase has tall ascenders, which rise above the cap line. The uppercase
characters present proportions similar to those of classical Roman capitals.

TYPOGRAPHIC CONSIDERATIONS
No Strike though
No Horizontal Scaling
No Drop Shadows
No Effects
Never use less than 120% Leading

OUR CORPORATE COLOURS
BRAND GUIDELINES
We were thinking that our primary colour palette consists of the Acid Green (Pantone 382) and Process Black.

We work closely with tquarly Ltd and would like to include their name on the card somewhere. I have attached images of the other brands that we work with as an idea or the small icons I have included that illustrate what we do?. I have very kindly been given permission to use any of the images off the files that I have included below, so I hope these help. I will include these below. I would be open to suggestions if it made the card more striking Can you do it?
Updates

Hi All, Just wanted to add a few thoughts but you are the guys with the creative visions (thats why are here) We are based in Wales, UK and we would be open to lots of different ideas on a theme but must be eye catching, Bold and FUN. If you can or think that the Welsh or any dragon could be put in there then go for it (its not a must have) We have also added some ideas for colour but again its over to you!! GO FOR IT ! Thanks and look forward to your visions! Owen

Hi All, Just thought I would sen through the contact details that need to be on the card. (if you want to play around with icons instead of the wording twitter, Facebook, go for it): Corvane Motion Limited Owen Pritchard Managing Director Mob: +44 (0)7582 913 406 e-mail: sales@corvanemotion.co.uk Web: Corvanemotion.co.uk twitter: @motionLetterbin Facebook: Corvane Motion Limited

```html
<!DOCTYPE html>
<html lang="en">
<head>
<meta charset="utf-8">
<title>Corvane Motion Limited – Business Cards</title>
<link rel="stylesheet" href="https://fonts.googleapis.com/css2?family=Open+Sans:wght@400;600&display=swap">
<style>
  :root {
    --backdrop: #e9e6e2;
    --paper: #ffffff;
    --navy: #0b0f3a;
    --stripe-blue: #1f64ad;
    --ink-light: #ffffff;
    --brand-navy: #0b0f3a;
    --brand-ring: #1d3f8c;
  }
  * { margin: 0; padding: 0; box-sizing: border-box; }
  html, body {
    width: 1200px; height: 900px; overflow: hidden;
    background: var(--backdrop);
    font-family: "Open Sans", Arial, sans-serif;
  }
  .canvas { position: relative; width: 1200px; height: 900px; }

  .card {
    position: absolute;
    overflow: hidden;
    box-shadow: 0 4px 14px rgba(0,0,0,0.18);
  }

  /* Front card */
  .card--front {
    left: 77px; top: 33px; width: 588px; height: 364px;
    background: var(--paper);
  }
  .card__bands { position: absolute; left: 0; top: 0; width: 588px; height: 364px; }

  .brand {
    position: absolute; left: 68px; top: 38px;
    display: flex; align-items: center; gap: 22px;
  }
  .brand__dot {
    width: 128px; height: 128px; border-radius: 50%;
    background: var(--brand-ring);
  }
  .brand__name {
    color: var(--brand-navy);
    font-weight: 400; font-size: 22px; line-height: 1.25;
    letter-spacing: 1px; text-transform: uppercase;
  }

  .person {
    position: absolute; right: 349px; top: 275px;
    text-align: right; color: var(--ink-light);
  }
  .person__name { font-weight: 600; font-size: 18px; line-height: 1.3; }
  .person__role { font-weight: 400; font-size: 14px; line-height: 1.3; }

  .contacts {
    position: absolute; left: 263px; top: 244px;
    list-style: none; color: var(--ink-light);
    font-size: 15px; line-height: 21px;
  }
  .contacts li { display: flex; align-items: center; gap: 9px; }
  .contacts svg { width: 12px; height: 12px; flex: none; fill: var(--ink-light); }
  .contacts .plain-mark { width: 11px; height: 11px; background: var(--ink-light); border-radius: 2px; flex: none; margin-right: 1px; }

  /* Back card */
  .card--back {
    left: 388px; top: 505px; width: 567px; height: 352px;
    background: var(--navy);
    display: flex; align-items: center; justify-content: center;
  }
  .card--back .brand__name {
    color: var(--ink-light); font-size: 26px; text-align: left;
  }
</style>
</head>
<body>
<main class="canvas">

  <section class="card card--front" aria-label="Business card, front">
    <svg class="card__bands" viewBox="0 0 588 364" aria-hidden="true">
      <polygon points="0,192 413,192 413,200 0,200" fill="#ffffff"/>
      <polygon points="0,200 405,200 384,228 0,228" fill="var(--stripe-blue)"/>
      <polygon points="0,230 393,230 415,192 588,192 588,364 0,364" fill="var(--navy)"/>
    </svg>

    <div class="brand">
      <span class="brand__dot"></span>
      <p class="brand__name">Corvane Motion<br>Limited</p>
    </div>

    <div class="person">
      <p class="person__name">Owen Pritchard</p>
      <p class="person__role">Managing Director</p>
    </div>

    <ul class="contacts">
      <li>
        <svg viewBox="0 0 24 24"><path d="M6.6 10.8a15 15 0 0 0 6.6 6.6l2.2-2.2a1 1 0 0 1 1-.25 11.4 11.4 0 0 0 3.6.57 1 1 0 0 1 1 1V20a1 1 0 0 1-1 1A17 17 0 0 1 3 4a1 1 0 0 1 1-1h3.5a1 1 0 0 1 1 1c0 1.25.2 2.45.57 3.57a1 1 0 0 1-.25 1z"/></svg>
        +44 (0)7582 913 406
      </li>
      <li>
        <svg viewBox="0 0 24 24"><path d="M2 5h20v14H2z M2 5l10 8 10-8" fill="none" stroke="#fff" stroke-width="2.4"/></svg>
        sales@corvanemotion.co.uk
      </li>
      <li>
        <svg viewBox="0 0 24 24"><circle cx="12" cy="12" r="10" fill="none" stroke="#fff" stroke-width="2"/><path d="M2 12h20M12 2c3 3 3 17 0 20M12 2c-3 3-3 17 0 20" fill="none" stroke="#fff" stroke-width="2"/></svg>
        Corvanemotion.co.uk
      </li>
      <li><span class="plain-mark"></span>@motionLetterbin</li>
      <li><span class="plain-mark"></span>Corvane Motion Limited</li>
    </ul>
  </section>

  <section class="card card--back" aria-label="Business card, back">
    <p class="brand__name">Corvane Motion<br>Limited</p>
  </section>

</main>
</body>
</html>
```